IT Company that provides secure IT solutions and services to our customers

We need business cards and a logo for a new IT Solutions company just created based in Kuala Lumpur, Malaysia. But will also be serving other countries in the region. We provide secure data, voice solutions on mobile platforms. Our first offering is encrypted voice and data solutions for IOS, Android, Windows and BlackBerry devices.

Target Market(s)

large organizations Govt, Police, Defence, Anti-corruption, Legal, highly regulated industries such as Health-care, Financial, Banking, Insurance,

Industry/Entity Type

Information Technology

Contact Information for Business Card

VelmoraNet (Logo - colour is ORVEX blue)Roshan Adeel Managing Director Kryption IT Sdn. Bhd.5th Floor, Block D, Wisma PLB,No.14 Jalan Seri Melor,50470, Kuala LumpurMalaysia

Font styles to use
Sans Serif

Colors
3176b5
ec1f27
fbed22

Requirements
Must have
• VelmoraNet all in Blue like ORVEX blue. A logo design perhaps a play of VN, K with a dangling T (colour can be any)
Nice to have
• I want a clean crisp card, not too busy, easy to read.

```html
<!DOCTYPE html>
<html lang="en">
<head>
<meta charset="UTF-8">
<title>VelmoraNet Business Card</title>
<link rel="stylesheet" href="https://fonts.googleapis.com/css2?family=Source+Sans+3:wght@400;600;700;800&display=swap">
<style>
  :root {
    --page-bg: #ecebe8;
    --brand-blue: #1f5fae;
    --card-blue: #1e5fae;
    --back-blue: #2a62b0;
    --back-mark: #2256a2;
    --accent-red: #d2232a;
    --card-white: #ffffff;
    --text-light: #ffffff;
  }
  * { margin: 0; padding: 0; box-sizing: border-box; }
  html, body {
    width: 1200px;
    height: 900px;
    overflow: hidden;
    background: var(--page-bg);
    font-family: "Source Sans 3", "Myriad Pro", Arial, sans-serif;
  }
  .canvas {
    position: relative;
    width: 1200px;
    height: 900px;
  }
  .card {
    position: absolute;
    height: 342px;
    overflow: hidden;
    box-shadow: 0 2px 6px rgba(0,0,0,0.12);
  }
  .card-front {
    left: 237px;
    top: 62px;
    width: 556px;
    background: var(--card-white);
  }
  .card-back {
    left: 457px;
    top: 518px;
    width: 560px;
    background: var(--back-blue);
  }
  .front-shapes {
    position: absolute;
    inset: 0;
  }
  .front-shapes .panel-blue { fill: var(--card-blue); }
  .front-shapes .rule-red { fill: var(--accent-red); }
  .brand-name {
    position: absolute;
    font-weight: 800;
    letter-spacing: -1px;
    line-height: 1;
    white-space: nowrap;
  }
  .card-front .brand-name {
    left: 34px;
    top: 44px;
    font-size: 68px;
    color: var(--brand-blue);
  }
  .card-back .brand-name {
    left: 0;
    right: 0;
    top: 132px;
    text-align: center;
    font-size: 66px;
    color: var(--back-mark);
  }
  .contact {
    position: absolute;
    right: 26px;
    top: 169px;
    text-align: right;
    color: var(--text-light);
    font-size: 15px;
    line-height: 20px;
  }
  .contact .person-name,
  .contact .company-name {
    font-size: 17px;
    font-weight: 700;
    line-height: 22px;
  }
  .contact .person-role { margin-bottom: 10px; }
</style>
</head>
<body>
<main class="canvas">
  <section class="card card-front">
    <svg class="front-shapes" width="556" height="342" viewBox="0 0 556 342" aria-hidden="true">
      <polygon class="rule-red" points="540,0 551,0 84,342 70,342"/>
      <polygon class="panel-blue" points="556,8 556,342 100,342"/>
    </svg>
    <div class="brand-name">VelmoraNet</div>
    <div class="contact">
      <p class="person-name">Roshan Adeel</p>
      <p class="person-role">Managing Director</p>
      <p class="company-name">Velmora Net</p>
      <p>Sdn. Bhd.5th Floor, Block D,</p>
      <p>Wisma PLB,No.14 Jalan Seri Melor,</p>
      <p>50470, Kuala Lumpur</p>
      <p>Malaysia</p>
    </div>
  </section>

  <section class="card card-back">
    <div class="brand-name">VelmoraNet</div>
  </section>
</main>
</body>
</html>
```